Meridale Bed Company Needs Business Card

Looking for a very nice looking business card. Creative but not extravagant. We sell beds and pillows across the U.S. and need something professional but catchy. I have attached the logo.

Name : Devin Holt
Title : President
Phone : (800) 471-2960
Email: sleep@quilmora.com
Website: www.quilmora.com

Can be single-sided or double-sided
horizontal or vertical

Can use Blues/Greys

Target Market(s)

Mass Market

Industry/Entity Type

Retail

Contact Information for Business Card

Name : Devin Holt
Title : President
Phone : (800) 471-2960
Email: sleep@quilmora.com
Website: www.quilmora.com

Requirements
Must have
• Clean, Modern, Smooth
• Can use Blues/Greys
• On the other side without the information - have something simple like www.quilmora.com or our logo
Nice to have
• Surprise me
Should not have
• Nothing crazy, nothing cluttered

```html
<!DOCTYPE html>
<html lang="en">
<head>
<meta charset="utf-8">
<title>Meridale Bed Company – Business Card</title>
<link rel="stylesheet" href="https://fonts.googleapis.com/css2?family=Quicksand:wght@300;500;700&display=swap">
<style>
  :root{
    --bg:#e9ebee;
    --card-back:#4b8cab;
    --card-back-mark:#6fb6d3;
    --card-front:#ffffff;
    --brand-blue:#2ea7df;
    --ink:#3a3a3a;
    --rule:#8a8a8a;
  }
  html,body{margin:0;padding:0;overflow:hidden;}
  body{
    width:1200px;height:769px;background:var(--bg);
    font-family:"Quicksand",sans-serif;position:relative;
  }
  .card{
    position:absolute;top:236px;width:520px;height:297px;
    box-shadow:0 6px 18px rgba(0,0,0,.18);
    box-sizing:border-box;overflow:hidden;
  }
  .card--back{left:45px;background:var(--card-back);
    display:flex;align-items:center;justify-content:center;}
  .card--front{left:635px;background:var(--card-front);}
  .wordmark{font-weight:300;letter-spacing:2px;line-height:1;white-space:nowrap;}
  .card--back .wordmark{color:var(--card-back-mark);font-size:90px;}
  .card--front .wordmark{
    position:absolute;right:64px;top:62px;
    color:var(--brand-blue);font-size:76px;
  }
  .person{
    position:absolute;right:300px;top:188px;text-align:right;
  }
  .person__name{color:var(--brand-blue);font-weight:700;font-size:20px;margin:0;}
  .person__title{color:var(--ink);font-weight:500;font-size:17px;margin:2px 0 0;}
  .divider{
    position:absolute;left:240px;top:182px;width:1px;height:80px;background:var(--rule);
  }
  .contact{
    position:absolute;left:258px;top:186px;margin:0;padding:0;list-style:none;
    color:var(--ink);font-weight:500;font-size:15px;
  }
  .contact li{display:flex;align-items:center;gap:8px;height:24px;}
  .contact svg{width:16px;height:16px;flex:none;}
</style>
</head>
<body>
  <section class="card card--back" aria-label="Card back">
    <span class="wordmark">quilmora</span>
  </section>

  <section class="card card--front" aria-label="Card front">
    <span class="wordmark">quilmora</span>

    <div class="person">
      <p class="person__name">Devin Holt</p>
      <p class="person__title">President</p>
    </div>

    <div class="divider"></div>

    <ul class="contact">
      <li>
        <svg viewBox="0 0 16 16" aria-hidden="true"><path fill="#2ea7df" d="M3 2h3l1 3-2 1.2a8 8 0 0 0 3.8 3.8L10 8l3 1v3c0 .8-.6 1.5-1.5 1.5A10.5 10.5 0 0 1 1.5 3.5C1.5 2.6 2.2 2 3 2z"/></svg>
        (800) 471-2960
      </li>
      <li>
        <svg viewBox="0 0 16 16" aria-hidden="true"><rect x="1" y="3.5" width="14" height="9" rx="1" fill="#2ea7df"/><path d="M1.5 4.2 8 9l6.5-4.8" fill="none" stroke="#fff" stroke-width="1.2"/></svg>
        sleep@quilmora.com
      </li>
      <li>
        <svg viewBox="0 0 16 16" aria-hidden="true"><circle cx="8" cy="8" r="7" fill="#2ea7df"/><ellipse cx="8" cy="8" rx="3" ry="7" fill="none" stroke="#fff" stroke-width="1"/><path d="M1 8h14" stroke="#fff" stroke-width="1"/></svg>
        www.quilmora.com
      </li>
    </ul>
  </section>
</body>
</html>
```